Home Fund Guide

Have clients check their mortgage qualifications before they go looking for a mortgage lender. This program gains access to your lenders credit report / 3 scores without impacting your credit scores.

```html
<!DOCTYPE html>
<html lang="en">
<head>
<meta charset="utf-8">
<title>Home Fund Guide – Business Card</title>
<link href="https://fonts.googleapis.com/css2?family=Roboto:wght@400;500;700&family=Roboto+Condensed:wght@400&display=swap" rel="stylesheet">
<style>
  :root {
    --backdrop: #6b6868;
    --card: #1a1a1a;
    --card-edge: #222222;
    --blue: #1f55c9;
    --green: #1fbf78;
    --text: #f2f2f2;
    --deboss: #2e2e2e;
    --deboss-mark: #262626;
  }
  * { margin: 0; padding: 0; box-sizing: border-box; }
  html, body { width: 1200px; height: 1200px; overflow: hidden; }
  body {
    background: var(--backdrop);
    font-family: "Roboto", Arial, sans-serif;
    position: relative;
  }
  .card {
    position: absolute;
    width: 593px;
    height: 349px;
    background: var(--card);
    border-radius: 26px;
    overflow: hidden;
    border: 1px solid var(--card-edge);
  }
  .card--front { left: 300px; top: 198px; }
  .card--back  { left: 292px; top: 636px; }

  /* Front */
  .front-brand {
    position: absolute;
    left: 0; right: 0; top: 72px;
    display: flex; flex-direction: column; align-items: center;
  }
  .front-brand__square {
    width: 150px; height: 112px;
    background: var(--deboss-mark);
    border-radius: 12px;
  }
  .front-brand__name {
    margin-top: 14px;
    font-size: 34px;
    font-weight: 500;
    color: var(--deboss);
    letter-spacing: 0.5px;
  }

  /* Back */
  .back-brand {
    position: absolute;
    left: 30px; width: 260px; top: 112px;
    display: flex; flex-direction: column; align-items: center;
  }
  .back-brand__square {
    width: 100px; height: 70px;
    background: var(--blue);
    border-radius: 8px;
  }
  .back-brand__name {
    margin-top: 14px;
    font-size: 28px;
    font-weight: 500;
    color: var(--blue);
    white-space: nowrap;
  }
  .contact {
    position: absolute;
    left: 320px; top: 68px;
    color: var(--text);
  }
  .contact__name { font-size: 25px; font-weight: 500; line-height: 1.2; }
  .contact__first { color: var(--blue); font-weight: 400; }
  .contact__last { color: var(--green); font-weight: 700; }
  .contact__role { font-size: 16px; margin-top: 2px; }
  .contact__list { list-style: none; margin-top: 18px; }
  .contact__item {
    display: flex; align-items: center;
    font-size: 15.5px; height: 22px;
  }
  .contact__icon { width: 14px; height: 14px; margin-right: 16px; flex: none; }
  .contact__address { font-size: 15.5px; line-height: 22px; margin-top: 8px; }

  .footer-band {
    position: absolute;
    left: 0; right: 0; bottom: 0; height: 40px;
    background: linear-gradient(90deg, var(--blue) 0%, #1a8aa8 55%, var(--green) 100%);
    display: flex; align-items: center; justify-content: center;
    font-family: "Roboto Condensed", "Arial Narrow", sans-serif;
    font-size: 13.5px;
    color: #ffffff;
    white-space: nowrap;
  }
</style>
</head>
<body>

<section class="card card--front" aria-label="Card front">
  <div class="front-brand">
    <div class="front-brand__square"></div>
    <div class="front-brand__name">HomeFundGuide</div>
  </div>
</section>

<section class="card card--back" aria-label="Card back">
  <div class="back-brand">
    <div class="back-brand__square"></div>
    <div class="back-brand__name">HomeFundGuide</div>
  </div>

  <div class="contact">
    <p class="contact__name"><span class="contact__first">Dana</span> <span class="contact__last">Carter</span></p>
    <p class="contact__role">Managing Director</p>
    <ul class="contact__list">
      <li class="contact__item">
        <svg class="contact__icon" viewBox="0 0 16 16" aria-hidden="true"><path fill="#1f55c9" d="M1 5c0-2 3-3 7-3s7 1 7 3v1h-4V5H5v1H1zM3 7h10l1 7H2z"/></svg>
        (877) 555-0148
      </li>
      <li class="contact__item">
        <svg class="contact__icon" viewBox="0 0 16 16" aria-hidden="true"><rect x="1" y="3" width="14" height="10" fill="#1fbf78"/><path d="M1 3l7 6 7-6M1 13l5-5M15 13l-5-5" stroke="#1a1a1a" stroke-width="1.4" fill="none"/></svg>
        Support@HomeFundGuide.org
      </li>
      <li class="contact__item">
        <svg class="contact__icon" viewBox="0 0 16 16" aria-hidden="true"><circle cx="8" cy="8" r="6.5" fill="#1f55c9"/><path d="M1.5 8h13M8 1.5v13M3 4.5h10M3 11.5h10" stroke="#1a1a1a" stroke-width="1"/><ellipse cx="8" cy="8" rx="3" ry="6.5" fill="none" stroke="#1a1a1a" stroke-width="1"/></svg>
        www.HomeFundGuide.org
      </li>
    </ul>
    <p class="contact__address">318 Maple Avenue, Suite 210,<br>Fairview, Oregon 97024</p>
  </div>

  <div class="footer-band">HomeFundGuide is Managed by Hale Financial, A 401(c)(3) Nonprofit Certified Credit Counselor</div>
</section>

</body>
</html>
```